Poster

I need a poster for my business, www.coastalsupperroutesnerja.example which some information about the most important activities (Sangria Tasting, Iberian Ham, Charcuteries & Sherry Wine Tasting, Sailboat Experiences and Picnic Experiences). A3 Format. Social media included (@coastalsupperroutescsr), contact information included.

```html
<!DOCTYPE html>
<html lang="en">
<head>
<meta charset="utf-8">
<title>Coastal Supper Routes Nerja – Poster</title>
<link rel="stylesheet" href="https://fonts.googleapis.com/css2?family=Bebas+Neue&family=Montserrat:wght@300;400;600&display=swap">
<style>
  :root {
    --paper: #ffffff;
    --amber: #f0a322;
    --charcoal: #4a4646;
    --ink: #3d3a3a;
    --light: #ffffff;
    --photo-top: #eeeeea;
    --photo-mid: #b9b4ad;
    --photo-low: #8a2a2a;
  }
  * { margin: 0; padding: 0; box-sizing: border-box; }
  html, body { width: 900px; height: 1200px; overflow: hidden; background: var(--paper); }
  .poster { position: relative; width: 900px; height: 1200px; background: var(--paper); }
  .panel { position: absolute; }
  .panel--amber { background: var(--amber); color: var(--ink); }
  .panel--charcoal { background: var(--charcoal); color: var(--light); }
  .title {
    font-family: "Bebas Neue", Impact, sans-serif;
    line-height: 0.95;
    letter-spacing: 0.5px;
  }
  .subtitle {
    font-family: "Montserrat", Arial, sans-serif;
    font-weight: 400;
    line-height: 1;
  }

  .sangria { left: 43px; top: 45px; width: 322px; height: 174px; padding: 20px 0 0 34px; }
  .sangria .title { font-size: 88px; }
  .sangria .subtitle { font-size: 53px; margin-top: 2px; margin-left: -4px; }

  .brand { position: absolute; left: 440px; top: 62px; width: 410px; height: 150px; display: flex; align-items: center; gap: 22px; }
  .brand__mark { width: 28px; height: 28px; background: var(--amber); flex: none; }
  .brand__name { font-family: "Bebas Neue", Impact, sans-serif; font-size: 56px; line-height: 0.95; color: var(--ink); }

  .tasting { left: 43px; top: 242px; width: 814px; height: 279px; padding: 34px 0 0 38px; }
  .tasting .title { font-size: 86px; line-height: 0.98; }
  .tasting .subtitle { font-size: 54px; font-weight: 300; margin-top: 4px; }

  .sailboat { left: 43px; top: 544px; width: 491px; height: 174px; padding: 22px 0 0 34px; }
  .picnic { left: 43px; top: 741px; width: 491px; height: 174px; padding: 22px 0 0 34px; }
  .sailboat .title, .picnic .title { font-size: 82px; }
  .sailboat .subtitle, .picnic .subtitle { font-size: 56px; font-weight: 300; margin-top: 4px; margin-left: -2px; }

  .photo {
    left: 561px; top: 544px; width: 290px; height: 367px;
    background: linear-gradient(180deg, var(--photo-top) 0%, var(--photo-top) 25%, var(--photo-mid) 55%, var(--photo-low) 80%, var(--photo-mid) 100%);
  }

  .contact { left: 43px; top: 939px; width: 814px; height: 221px; text-align: center; font-family: "Montserrat", Arial, sans-serif; }
  .contact__phone { font-weight: 300; font-size: 54px; padding-top: 28px; letter-spacing: 1px; }
  .contact__web { font-size: 29px; font-weight: 400; margin-top: 24px; }
  .contact__web strong { color: var(--amber); font-weight: 600; }
  .contact__social { font-size: 22px; font-weight: 300; margin-top: 24px; display: flex; align-items: center; justify-content: center; gap: 14px; }
  .contact__dot { width: 28px; height: 28px; border-radius: 50%; background: var(--amber); }
</style>
</head>
<body>
<main class="poster">
  <section class="panel panel--amber sangria">
    <h2 class="title">Sangria</h2>
    <p class="subtitle">TASTING</p>
  </section>

  <div class="brand">
    <span class="brand__mark"></span>
    <h1 class="brand__name">COASTAL SUPPER<br>ROUTES NERJA</h1>
  </div>

  <section class="panel panel--charcoal tasting">
    <h2 class="title">IBERIAN HAM,<br>CHARCUTERIES &amp; SHERRY</h2>
    <p class="subtitle">WINE TASTING</p>
  </section>

  <section class="panel panel--amber sailboat">
    <h2 class="title">SAILBOAT</h2>
    <p class="subtitle">EXPERIENCES</p>
  </section>

  <section class="panel panel--charcoal picnic">
    <h2 class="title">PICNIC</h2>
    <p class="subtitle">EXPERIENCES</p>
  </section>

  <div class="panel photo" role="img" aria-label="Glasses of sangria and white wine on a terrace table with palm trees behind"></div>

  <footer class="panel panel--charcoal contact">
    <p class="contact__phone">+34 600 12 34 56</p>
    <p class="contact__web">www.<strong>coastalsupperroutesnerja</strong>.example</p>
    <p class="contact__social"><span class="contact__dot"></span>@coastalsupperroutescsr</p>
  </footer>
</main>
</body>
</html>
```